Creation of an elegant and modern turnkey Shopify website

Hello,

We are a new company specializing in the sale of above-ground pools. We want to create a turnkey website, ideally using Shopify. For now, we need a "showcase" site, not an e-commerce platform, with four tabs:

Home Page (an overall presentation of the company)
Our Products (an overview of all the above-ground pools we sell)
Our Projects (a page inspired by Instagram to showcase photos of our future projects)
Contact (a page with all our contact information and a contact form)

We are looking to create a highly visual, elegant, and modern website with vibrant splashes of color. We will provide the text, photos (along with instructions on where to place them on each page), and all other necessary information as attachments.

Thank you in advance for your proposals!

The Brisa Lagoon Team

Target Market(s)

Targeted at Swiss customers (a translator will need to be installed for different languages)

Industry/Entity Type

Sale of customised above-ground pools

Coding

Coded - Design and coding required

Font styles to use
Sans Serif

Colors
0094D4
00A9DD
6FCCEA
C7EBF8
E9F6FB
00AB8E
00BBA5
67D7C9
C6EFE9
E9F9F6

Requirements
Must have
• A stunning, elegant and modern look
Nice to have
• Inspiration from the colors of our logo throughout the site, but in an elegant way
Should not have
• An overly classic look for swimming pool sites

```html
<!DOCTYPE html>
<html lang="en">
<head>
<meta charset="utf-8">
<title>Brisa Lagoon – Above-Ground Pools</title>
<link href="https://fonts.googleapis.com/css2?family=Josefin+Sans:wght@300;400;600&family=Jost:wght@300;400&display=swap" rel="stylesheet">
<style>
:root{
  --blue:#0094D4;
  --blue-2:#00A9DD;
  --blue-3:#6FCCEA;
  --blue-4:#C7EBF8;
  --green:#00AB8E;
  --green-2:#00BBA5;
  --green-3:#67D7C9;
  --ink:#111;
  --white:#fff;
  --grey:#eeeeee;
}
*{box-sizing:border-box;margin:0;padding:0}
html,body{width:1200px;height:5195px;overflow:hidden}
body{position:relative;background:var(--white);font-family:'Jost',sans-serif;color:var(--ink)}
.abs{position:absolute}
.photo{position:absolute}
h1,h2,h3,.brand,.card-label{font-family:'Josefin Sans',sans-serif;font-weight:400}

/* header */
.phone{left:111px;top:32px;font-size:15px;color:#333;display:flex;align-items:center;gap:6px}
.brand{left:0;width:1200px;top:30px;text-align:center;font-size:44px;color:var(--blue);letter-spacing:1px;font-weight:300}
.header-icons{left:990px;top:30px;display:flex;gap:20px}
.nav{top:125px;left:0;width:1200px;font-size:15px;color:#333}
.nav a{position:absolute;color:#333;text-decoration:none;white-space:nowrap;transform:translateX(-50%)}
.welcome{top:168px;left:0;width:1200px;text-align:center;font-size:60px;font-weight:400}
.welcome span{color:var(--blue)}
.hero{left:111px;top:246px;width:978px;height:405px;background:linear-gradient(135deg,#2f5a24,#4d7b33 45%,#1f78b8 70%,#3b6a2a)}
.slider-bar{left:111px;top:651px;width:978px;height:45px;background:var(--grey);display:flex;justify-content:center;align-items:center;gap:6px}

/* feature panels */
.panel{position:absolute;color:var(--white)}
.panel h2{font-size:40px;line-height:1.3;margin-bottom:28px}
.panel p{font-size:17px;line-height:1.8;font-weight:300}
.bg-blue{background:var(--blue)}
.bg-green{background:var(--green)}

/* why choose */
.why{left:0;top:1735px;width:1200px;height:1676px;background:linear-gradient(180deg,var(--blue) 0%,var(--blue-2) 30%,var(--green) 80%,var(--green) 100%)}
.why h2{position:absolute;top:92px;width:1200px;text-align:center;color:var(--white);font-size:40px;line-height:1.35}
.card-img{position:absolute;width:478px;height:365px}
.card-label{position:absolute;width:478px;text-align:center;color:var(--white);font-size:30px;display:flex;justify-content:center;align-items:center;gap:10px}

/* footer */
.footer{left:0;top:4605px;width:1200px;height:590px;background:var(--blue);color:var(--white)}
.footer .brand{top:90px;color:var(--white);font-size:72px;line-height:1}
.subscribe{position:absolute;top:272px;width:1200px;text-align:center;font-size:32px;font-weight:300}
.email{position:absolute;left:319px;top:341px;width:563px;height:72px;border:2px solid var(--white);display:flex;align-items:center;justify-content:space-between;padding:0 22px;font-size:24px;font-weight:300}
.copyright{position:absolute;top:476px;width:1200px;height:114px;border-top:1px solid rgba(255,255,255,.5);display:flex;justify-content:center;align-items:center;font-size:24px;font-family:'Jost',sans-serif}
.btn{display:inline-block;background:var(--white);color:var(--ink);font-family:'Josefin Sans',sans-serif;font-size:17px;padding:18px 24px;margin-top:32px}
</style>
</head>
<body>

<!-- Header -->
<div class="abs phone">
  <svg width="14" height="14" viewBox="0 0 24 24"><path fill="#333" d="M6.6 10.8a15 15 0 006.6 6.6l2.2-2.2c.3-.3.7-.4 1-.2 1.1.4 2.3.6 3.6.6.6 0 1 .4 1 1V20c0 .6-.4 1-1 1C10.6 21 3 13.4 3 4c0-.6.4-1 1-1h3.5c.6 0 1 .4 1 1 0 1.3.2 2.5.6 3.6.1.3 0 .7-.2 1z"/></svg>
  Call : 555-010-2244
</div>
<div class="abs brand">BRISA LAGOON</div>
<div class="abs header-icons">
  <svg width="16" height="16" viewBox="0 0 24 24"><circle cx="12" cy="7" r="5" fill="#222"/><path d="M2 23c0-6 4.5-9 10-9s10 3 10 9z" fill="#222"/></svg>
  <svg width="18" height="16" viewBox="0 0 24 22"><path d="M1 2h4l3 12h12l3-9H7" fill="none" stroke="#222" stroke-width="3"/><circle cx="9" cy="19" r="2" fill="#222"/><circle cx="19" cy="19" r="2" fill="#222"/></svg>
  <svg width="16" height="16" viewBox="0 0 24 24"><rect x="3" y="3" width="18" height="18" fill="none" stroke="#222" stroke-width="2.5"/><path d="M8 8h8v8H8z" fill="#222"/></svg>
</div>
<nav class="abs nav">
  <a style="left:411px">Home</a>
  <a style="left:527px">Our Products</a>
  <a style="left:662px">Our Projects</a>
  <a style="left:780px">Contact</a>
</nav>
<h1 class="abs welcome">Welcome To <span>Brisa Lagoon</span></h1>
<div class="abs hero" role="img" aria-label="Aerial view of a round above-ground pool set in a green lawn among shrubs"></div>
<div class="abs slider-bar">
  <svg width="12" height="16" viewBox="0 0 12 16"><path d="M9 2L3 8l6 6" fill="none" stroke="#222" stroke-width="2.5"/></svg>
  <svg width="88" height="18" viewBox="0 0 88 18"><circle cx="9" cy="9" r="7" fill="none" stroke="#222" stroke-width="1.5"/><circle cx="32" cy="9" r="7" fill="#222"/><circle cx="55" cy="9" r="7" fill="none" stroke="#222" stroke-width="1.5"/><circle cx="78" cy="9" r="7" fill="none" stroke="#222" stroke-width="1.5"/></svg>
  <svg width="12" height="16" viewBox="0 0 12 16"><path d="M3 2l6 6-6 6" fill="none" stroke="#222" stroke-width="2.5"/></svg>
</div>

<!-- Services -->
<div class="panel bg-blue" style="left:111px;top:770px;width:603px;height:370px;padding:62px 44px">
  <h2>Personalized Services</h2>
  <p>We understand that every garden and client is unique. That's why we offer personalized services, from design to installation and after-sales support. Our team of experts is here to answer all your questions and guide you throughout your project.</p>
</div>
<div class="photo" style="left:714px;top:770px;width:375px;height:370px;background:linear-gradient(160deg,#c7e3f0,#7fb36a 60%,#5f8f44)" role="img" aria-label="Child climbing the ladder of an above-ground pool"></div>
<div class="photo" style="left:111px;top:1142px;width:603px;height:470px;background:linear-gradient(120deg,#1aa9dd,#4fd0ee 55%,#5aa83e 85%)" role="img" aria-label="Child relaxing on an inflatable ring in a pool"></div>
<div class="panel bg-green" style="left:714px;top:1142px;width:375px;height:470px;padding:30px 42px">
  <h2 style="margin-bottom:22px">Guaranteed Satisfaction</h2>
  <p>Your satisfaction is our top priority. We are committed to providing you with exceptional service and the highest quality products. Join our community of satisfied customers who are already enjoying their custom above-ground pools. 10-Year Warranty!</p>
</div>

<!-- Why choose -->
<section class="abs why">
  <h2>Why Choose<br>Our Above-Ground Pools?</h2>

  <div class="card-img" style="left:111px;top:260px;background:linear-gradient(135deg,#2a8fd8,#58b9ec 60%,#1e6fb8)" role="img" aria-label="Two people enjoying the water in a pool"></div>
  <div class="card-label" style="left:111px;top:640px">Superior Quality <svg width="30" height="14" viewBox="0 0 30 14"><path d="M0 7h24M18 1l8 6-8 6" fill="none" stroke="#fff" stroke-width="3"/></svg></div>

  <div class="card-img" style="left:611px;top:260px;background:linear-gradient(180deg,#e9f2f5,#a8cbd6 40%,#2f9fd6 70%,#1a7cbf)" role="img" aria-label="Rectangular above-ground pool beside a house"></div>
  <div class="card-label" style="left:611px;top:640px">Elegant Design <svg width="30" height="14" viewBox="0 0 30 14"><path d="M0 7h24M18 1l8 6-8 6" fill="none" stroke="#fff" stroke-width="3"/></svg></div>

  <div class="card-img" style="left:111px;top:716px;background:linear-gradient(180deg,#2f4d2a,#2d7dc0 30%,#6fc0e6)" role="img" aria-label="Pool being cleaned with a skimmer net"></div>
  <div class="card-label" style="left:111px;top:1096px">Custom and Tailor-Made <svg width="30" height="14" viewBox="0 0 30 14"><path d="M0 7h24M18 1l8 6-8 6" fill="none" stroke="#fff" stroke-width="3"/></svg></div>

  <div class="card-img" style="left:611px;top:716px;background:linear-gradient(160deg,#2f6b3a,#2c8fd6 30%,#7ad0ef)" role="img" aria-label="Hand holding a pool net over clear water"></div>
  <div class="card-label" style="left:611px;top:1096px">Easy Installation <svg width="30" height="14" viewBox="0 0 30 14"><path d="M0 7h24M18 1l8 6-8 6" fill="none" stroke="#fff" stroke-width="3"/></svg></div>

  <div class="card-img" style="left:361px;top:1155px;background:linear-gradient(180deg,#2c3a24,#d9dbd8 45%,#b7b2a6 75%,#8a8274)" role="img" aria-label="Round above-ground pool wall installed on sand"></div>
  <div class="card-label" style="left:361px;top:1535px">Constant Innovation <svg width="30" height="14" viewBox="0 0 30 14"><path d="M0 7h24M18 1l8 6-8 6" fill="none" stroke="#fff" stroke-width="3"/></svg></div>
</section>

<!-- Transform -->
<div class="photo" style="left:111px;top:3510px;width:375px;height:562px;background:linear-gradient(180deg,#7fd2e8,#bfe6ef 40%,#d9b9a0 60%,#55b8c4)" role="img" aria-label="Person in a wide sun hat sitting by a pool"></div>
<div class="panel bg-blue" style="left:486px;top:3510px;width:603px;height:562px;padding:50px 50px">
  <h2 style="font-size:40px;line-height:1.35;margin-bottom:36px">Transform Your Garden with Our Premium Above-Ground Pools!</h2>
  <p style="margin-bottom:26px">Achieve your dreams with our custom, tailor-made above-ground pools.</p>
  <p>Imagine an exceptional relaxation and leisure space right in your own backyard. With our unparalleled expertise and commitment to excellence, we create above-ground pools that exceed all expectations. Our exclusive, custom-designed models are crafted to combine style, durability, and innovation, offering a unique and refined experience.</p>
</div>
<div class="panel bg-green" style="left:111px;top:4074px;width:603px;height:412px;padding:44px 40px">
  <h2 style="margin-bottom:22px">Contact Us Today</h2>
  <p>Don't wait any longer to transform your garden into a wellness oasis. Contact us today to discover our range of customizable above-ground pools and get a tailored quote. Dive into a world of infinite possibilities with [Your Company Name].</p>
  <span class="btn">We Bring Your Pool Dreams to Life!</span>
</div>
<div class="photo" style="left:714px;top:4074px;width:375px;height:412px;background:linear-gradient(135deg,#e3f3f5,#8fd0cc 45%,#f2f6f6 60%,#3fa892)" role="img" aria-label="Striped teal and white beach cabin"></div>

<!-- Footer -->
<footer class="abs footer">
  <div class="abs brand">BRISA LAGOON</div>
  <div class="subscribe">Subscribe to our emails</div>
  <div class="email"><span>Email</span><svg width="26" height="14" viewBox="0 0 26 14"><path d="M0 7h22M16 1l7 6-7 6" fill="none" stroke="#fff" stroke-width="2.5"/></svg></div>
  <div class="copyright">© 2024 Brisa Lagoon . All Rights Reserved</div>
</footer>

</body>
</html>
```